Eco-friendly waste company needs flyer design to promote collections

We need a flyer to promote our new small item collection service, offering cheaper waste collections to customers who usually would not want to pay for our high-eco performance business (we are expensive compared to companies who dispose of their waste in less eco-friendly ways). This flyer needs to be professional, informational, and classy to appeal to corporate office-based customers. We want photos used where possible, not cartoon or illustrations of objects we collect. I will attach our logo in various designs, and am really open to design options. We have a website that is ourdated, uses cartoons etc, and this is not landing well with our customer base so we want to move away from that kind of design. I need an A5-sized flyer, double sided. Please ask me if you have any questions!
Hi all,
Thank you all so much for so many wonderful designs, I will be looking through all of these tomorrow with my CEO and then I will update the project status again.
Thanks!!
Kind regards,
Nora

Hi all,
Thanks!!
Kind regards,
Nora

```html
<!DOCTYPE html>
<html lang="en">
<head>
<meta charset="utf-8">
<title>Terra Clear – Small Item Collection Flyer</title>
<link rel="stylesheet" href="https://fonts.googleapis.com/css2?family=Rubik:wght@400;500;700&family=Barlow+Condensed:wght@500;600;700&display=swap">
<style>
:root{
  --green:#35a98a;
  --green-dark:#2b8f74;
  --ink:#2b2b2b;
  --charcoal:#3a3a36;
  --black:#111;
  --paper:#ffffff;
  --paper-soft:#f1f2f1;
  --stage:#3b3b3b;
  --muted:#e9e9e9;
}
*{box-sizing:border-box;margin:0;padding:0}
html,body{width:1200px;height:776px;overflow:hidden;background:var(--stage)}
body{font-family:"Rubik",Arial,sans-serif;color:var(--ink);position:relative}

.flyer{position:absolute;top:84px;width:432px;height:610px;background:linear-gradient(160deg,var(--paper) 40%,var(--paper-soft));overflow:hidden;box-shadow:0 8px 20px rgba(0,0,0,.35);display:flex;flex-direction:column}
.flyer--front{left:150px;display:block}
.flyer--back{left:618px}

/* brand mark (name only) */
.brand{display:flex;align-items:center;gap:8px;font-family:"Rubik",sans-serif;font-weight:700;font-size:17px;line-height:1.05;letter-spacing:.5px}
.brand__dot{width:14px;height:14px;border-radius:50%;flex:none}

/* ---------- front ---------- */
.front-head{display:flex;justify-content:flex-end;align-items:center;gap:14px;padding:40px 28px 0 20px;height:150px}
.front-head__title{text-align:right;font-weight:700;font-size:22px;line-height:1.08;color:var(--ink)}
.front-head__title .hl{color:var(--green)}
.front-head__rule{width:2px;height:92px;background:var(--ink)}
.front-head .brand{color:var(--green);width:90px}
.front-head .brand__dot{background:var(--green)}

.offer{position:relative;height:62px;margin-top:8px}
.offer__band{position:absolute;right:0;top:0;width:300px;height:52px;background:var(--green);color:#fff;font-size:13.5px;line-height:1.3;padding:8px 12px 0 104px}
.offer__tag{position:absolute;left:0;top:26px;width:218px;height:34px;background:var(--black);color:#fff;font-size:8.5px;line-height:1.35;padding:5px 10px 0 20px}

.examples{padding:14px 30px 0 30px}
.examples__title{font-family:"Barlow Condensed",sans-serif;font-weight:700;font-size:17px;color:var(--green);letter-spacing:.3px}
.examples__cols{display:flex;gap:14px;margin-top:2px}
.ticks{list-style:none;font-family:"Barlow Condensed",sans-serif;font-weight:600;font-size:11.5px;line-height:1.55;color:var(--ink)}
.ticks li{position:relative;padding-left:15px}
.ticks li::before{content:"";position:absolute;left:0;top:5px;width:8px;height:8px;border:1px solid var(--green)}
.ticks li::after{content:"";position:absolute;left:2px;top:5px;width:3px;height:5px;border:solid var(--green);border-width:0 1.5px 1.5px 0;transform:rotate(40deg)}
.examples__cols .ticks:first-child{width:140px}

.divider{height:2px;margin:10px 30px;background:linear-gradient(90deg,transparent,#bbb 20%,#bbb 80%,transparent)}
.challenge{text-align:center;font-size:11px;line-height:1.4;color:var(--ink)}

.contact{display:flex;justify-content:center;align-items:center;gap:10px;padding:2px 20px 0}
.contact__ask{text-align:right;font-size:13px;line-height:1.25}
.contact__rule{width:1px;height:44px;background:var(--ink)}
.contact__email{font-size:9px;font-weight:500;color:var(--green)}
.contact__phone{display:flex;align-items:center;gap:6px;font-size:8.5px;line-height:1.05}
.contact__phone b{font-family:"Barlow Condensed",sans-serif;font-size:24px;font-weight:700;color:var(--green);letter-spacing:1px}

.conditions{position:absolute;left:0;bottom:0;width:100%;height:80px;background:var(--green);color:#fff;text-align:center;font-family:"Barlow Condensed",sans-serif;font-weight:600;font-size:13px;line-height:1.3;padding-top:28px}
.conditions__tag{position:absolute;left:50%;top:-10px;transform:translateX(-50%);background:var(--black);padding:4px 26px;font-size:11.5px;clip-path:polygon(6% 0,100% 0,94% 100%,0 100%)}

/* ---------- back ---------- */
.back-head{flex:none;background:var(--green);height:116px;display:flex;align-items:center;justify-content:center;gap:14px;padding:10px 18px 0}
.back-head__title{color:#fff;font-weight:500;font-size:21px;line-height:1.12;text-align:center}
.back-head__rule{width:2px;height:78px;background:#fff}
.back-head .brand{color:#fff;width:80px}
.back-head .brand__dot{background:#fff}

.hazard{flex:none;padding:10px 26px 12px 30px}
.hazard__title{font-weight:700;font-size:13.5px;color:var(--green)}
.hazard .ticks{font-size:9.5px;line-height:1.35;margin-top:6px}
.hazard .ticks li::before{top:3px}
.hazard .ticks li::after{top:3px}
.price{color:var(--green)}

.data{flex:none;background:var(--charcoal);color:#fff;padding:16px 28px 16px 30px;height:200px}
.data__title{font-weight:700;font-size:14px;line-height:1.15}
.data__intro{font-size:8.3px;line-height:1.5;margin-top:8px;color:#e6e6e6}
.data__sub{font-weight:700;font-size:14px;margin-top:8px}
.data__cols{display:flex;gap:14px;margin-top:4px}
.data .ticks{color:#fff;font-size:10.5px;line-height:1.5;text-transform:uppercase}
.data .ticks li::before{border-color:#fff}
.data .ticks li::after{border-color:#fff}

.back-foot{padding:22px 26px 0;text-align:center;font-size:8.8px;line-height:1.6;color:var(--ink)}
.back-foot p+p{margin-top:6px}
</style>
</head>
<body>

<section class="flyer flyer--front" aria-label="Small item collection flyer, front">
  <header class="front-head">
    <h1 class="front-head__title"><span class="hl">Do you have</span><br>small or single items<br><span class="hl">that cost too much</span><br>to dispose of?</h1>
    <div class="front-head__rule"></div>
    <div class="brand"><span class="brand__dot"></span>TERRA CLEAR</div>
  </header>

  <div class="offer">
    <div class="offer__band">We can collect items for<br>£25 each on Wednesdays.</div>
    <div class="offer__tag">Are you located in Central London?<br>Terra Clear has the solution for you.</div>
  </div>

  <div class="examples">
    <h2 class="examples__title">EXAMPLE ITEMS ARE:</h2>
    <div class="examples__cols">
      <ul class="ticks">
        <li>Printers</li><li>Office furniture</li><li>Whiteboards</li><li>Shredders</li><li>PC or television monitors</li><li>Fans</li>
      </ul>
      <ul class="ticks">
        <li>Plants and planter boxes</li><li>Books and magazines (max 25kg)</li><li>Pallet</li><li>Packaging (cardboard boxes, polystyrene, plastic etc.)</li><li>Paints and chemicals (max 7 litres)</li><li>Light bulbs and fluorescent tubes (max 10 pieces)</li>
      </ul>
    </div>
  </div>

  <div class="divider"></div>
  <p class="challenge">We can take most things you can't put in your normal bins<br>CHALLENGE US!</p>
  <div class="divider"></div>

  <div class="contact">
    <p class="contact__ask">If you have any questions<br>please email us at</p>
    <div class="contact__rule"></div>
    <div>
      <p class="contact__email">bookings@terraclearwaste.com</p>
      <p class="contact__phone"><span>or call<br>us on</span><b>020-3946-0285</b></p>
    </div>
  </div>

  <footer class="conditions">
    <span class="conditions__tag">CONDITIONS OF OFFER:</span>
    PRICE IS EXCLUSIVE OF VAT.<br>
    Eligible postcodes: EC1, EC2, EC3, EC4, WC1, WC2, W1, SW1, SE1, E1, E2, N1, NW1
  </footer>
</section>

<section class="flyer flyer--back" aria-label="Hazardous items and data destruction flyer, back">
  <header class="back-head">
    <h1 class="back-head__title">Need to get rid of<br>items which can't go<br>in your normal bin?</h1>
    <div class="back-head__rule"></div>
    <div class="brand"><span class="brand__dot"></span>TERRA CLEAR</div>
  </header>

  <div class="hazard">
    <h2 class="hazard__title">We collect the following hazardous items:</h2>
    <ul class="ticks">
      <li>Paint - <span class="price">£4 per litre</span></li>
      <li>Fluorescent tubes and bulbs - <span class="price">£4 each</span></li>
      <li>Cooking oil / hydraulic oil / hazardous liquids - from <span class="price">£5 per litre</span></li>
      <li>TV / Computer monitors - <span class="price">£10 each</span></li>
      <li>Batteries - from <span class="price">£5 per kilo</span> (depends on type)</li>
      <li>Gas bottles &amp; fire extinguishers - <span class="price">£35 each</span> Fridges - <span class="price">£40</span> for a small fridge, <span class="price">£125</span> for a commercial fridge, <span class="price">£200</span> for an ammonia fridge each</li>
      <li>Air conditioners - <span class="price">£30 each</span></li>
    </ul>
  </div>

  <div class="data">
    <h2 class="data__title">NEED TO SECURELY DESTROY DATA ON YOUR<br>COMPUTER OR SERVER?</h2>
    <p class="data__intro">We can securely collect and wipe your data-holding electrical items, allowing for their safe reuse. Items that fail the wiping process will be securely shredded and recycled.</p>
    <h3 class="data__sub">Items include:</h3>
    <div class="data__cols">
      <ul class="ticks"><li>Computers</li><li>Laptops</li><li>Servers</li></ul>
      <ul class="ticks"><li>Routers</li><li>Switches</li><li>Mobile phones</li></ul>
      <ul class="ticks"><li>Landline phones</li><li>Printers with memory</li><li>Photocopiers with memory</li></ul>
    </div>
  </div>

  <footer class="back-foot">
    <p>We can provide certificates confirming data secure destruction, either through securing wiping and reuse, or through shredding and recycling.</p>
    <p>We can also securely destroy any paper, files, documents etc with our shredding service.</p>
  </footer>
</section>

</body>
</html>
```